New App: 4 Page Design - Updated Brief

We need an indicative design for our new app 'Kit Runner', a delivery service for tools and hardware in Sydney, Australia.

Imagine a service which copies the blue print of Zolvo Meals, but for tools and Hardware. Where builders and tradespeople are stuck on-site at work and need a tool to be delivered to them on-site, same day. They can jump onto this app and in-put their address, then select an item from the catalogue and confirm the order. Once the order has been collected and due for delivery a map will show the location of the delivery driver.

We'd like 4 pages designed.

1st page) Loading page, similar to but not the same as the ZolvoMeals example attached.

2nd page) Home page - featuring the logo and some icons which direct users around the website. (Please see link to design example: https://www.zolvomeals.example/au?ref_id=a1b2c3d4-e5f6-47a8-9b0c-d1e2f3a4b5c6 )

3rd page) A page which depicts the catalogue of tools and hardware (showing generic tools available (Please see link to design example https://www.trellmart.example/products/building-hardware).

4th page) We'd like a page which shows a map, tracking the delivery, from the hardware store, to the location of the purchaser, exactly like any typical zolvo delivery service.

Please see the below website for design guidance and ideas

https://www.trellmart.example/?src=ab.cd&ref=Xy7QpLm3Rt9Vw2KsNh4Bf8JdZc6GaT1YeUo5Mi0Wq3ErPx7Ls2Dn9Hv4Ck8Fj6Bg1Az5Tm3Ry0Qu7Wp2Xo4Zi9Ke6Jl8Nb3Vc1Sd5Ph7Mf_abc

Target Market(s)

Construction industry, tradespeople

Industry/Entity Type

Construction and Tradesmen

Colors

Designer to choose colors to be used in the design.

Requirements
Must have
• Desired Colour schemes: up to the designer but no bright colours
Nice to have
• An icon bar at the bottom of the page that directs you to the various pages on the app. Example shown in the attachments
Should not have
• An exact copy of the Zolvo App

```html
<!DOCTYPE html>
<html lang="en">
<head>
<meta charset="utf-8">
<title>Kit Runner – App Screens</title>
<link href="https://fonts.googleapis.com/css2?family=Inter:wght@400;500;600;700;800&display=swap" rel="stylesheet">
<style>
:root{
  --green:#1db965;
  --ink:#111111;
  --muted:#8a8a8a;
  --field:#f1f1f1;
  --card-shadow:0 1px 4px rgba(0,0,0,.09);
  --frame:#000000;
  --paper:#ffffff;
}
*{box-sizing:border-box}
html,body{margin:0;padding:0}
body{width:1136px;height:1200px;overflow:hidden;position:relative;background:var(--paper);font-family:"Inter",sans-serif;color:var(--ink)}
.icon-defs{position:absolute;width:0;height:0}

.phone{position:absolute;width:191px;border:3px solid var(--frame);border-radius:13px;background:var(--paper);overflow:hidden}
.phone.mini{transform:scale(.895);transform-origin:0 0;height:419px}

.status{position:absolute;top:7px;left:10px;right:10px;display:flex;justify-content:space-between;align-items:center;font-size:7px;font-weight:600;z-index:3}
.status svg{width:26px;height:6px}
.status.light{color:#fff}

.splash{display:flex;align-items:center;justify-content:center}
.splash-mark{font-size:13px;font-weight:700;color:var(--green);letter-spacing:.2px}

.app-head{position:absolute;top:25px;left:10px;right:10px;display:flex;align-items:center;height:18px}
.app-head .menu{width:9px;height:9px;color:var(--green)}
.wordmark{margin-left:12px;font-size:13px;font-weight:700;color:var(--green)}
.avatar{margin-left:auto;width:15px;height:15px;border-radius:50%;background:linear-gradient(135deg,#6d6a66,#c9c4bd)}
.home-body{position:absolute;top:66px;left:0;right:0}
.cat-card{margin:0 8px;padding:7px 8px 7px;border-radius:4px;box-shadow:var(--card-shadow)}
.row-title{display:flex;justify-content:space-between;align-items:baseline}
.row-title h3{margin:0;font-size:9.5px;font-weight:600}
.see-all{font-size:6.5px;color:var(--green)}
.cat-grid{display:grid;grid-template-columns:repeat(4,1fr);gap:5px;margin-top:9px}
.cat-item{text-align:center}
.cat-thumb{width:31px;height:31px;border-radius:8px;margin:0 auto}
.cat-item span{display:block;margin-top:3px;font-size:5.5px;line-height:1.3}

.hero{margin:14px 10px 0;height:150px;border-radius:3px;padding:11px 11px;background:linear-gradient(100deg,#27b866,#45ca81 55%,#66da9b)}
.hero h2{margin:0 0 13px;color:#fff;font-size:10.5px;font-weight:600;line-height:1.2;width:130px}
.field{height:26px;border-radius:3px;display:flex;align-items:center;padding:0 8px;font-size:6.8px;margin-bottom:6px;background:#eaf8f0;color:var(--muted)}
.field.white{background:#fff;color:var(--ink)}
.field svg{width:7px;height:7px;margin-right:6px;flex:none}
.field .chev{margin:0 0 0 auto;width:7px}
.find-btn{margin-top:12px;height:25px;border-radius:3px;background:#000;color:#fff;font-size:8px;font-weight:600;display:flex;align-items:center;justify-content:center}

.section{margin:20px 0 0 9px}
.section .row-title{margin-right:10px}
.strip{display:flex;gap:6px;margin-top:9px;overflow:hidden}
.product{flex:none;width:59px}
.product-img{height:61px;border-radius:3px;box-shadow:var(--card-shadow)}
.product p{margin:5px 0 0;font-size:6px;line-height:1.3}
.price-row{display:flex;justify-content:space-between;align-items:center;margin-top:4px}
.price{font-size:8px;font-weight:600;color:var(--green)}
.rate{font-size:5px}
.shop-img{height:40px;border-radius:2px}
.shop p{margin:5px 0 0;font-size:6.5px}
.shop small{display:flex;align-items:center;gap:2px;font-size:5.5px;color:var(--muted);margin-top:3px}
.shop small svg{width:5px;height:5px;color:var(--green)}

.tabbar{position:absolute;left:0;right:0;bottom:0;height:42px;background:#fff;display:grid;grid-template-columns:repeat(4,1fr);padding-top:9px}
.tab{text-align:center;font-size:6px;color:var(--muted);position:relative}
.tab svg{display:block;width:11px;height:11px;margin:0 auto 3px;color:#555}
.tab.on{color:var(--green)}
.tab.on svg{color:var(--green)}
.badge{position:absolute;top:-3px;left:50%;margin-left:2px;width:6px;height:6px;border-radius:50%;background:var(--green);color:#000;font-size:4px;line-height:6px;text-align:center}

.page-head{position:absolute;top:27px;left:10px;right:10px;display:flex;align-items:center;height:16px}
.page-head .back{width:8px;height:8px}
.page-head h1{margin:0 0 0 8px;font-size:11px;font-weight:600}
.head-actions{margin-left:auto;display:flex;align-items:center;gap:10px}
.head-actions .cart{width:12px;height:12px;position:relative}
.head-actions .cart svg{width:12px;height:12px}
.head-actions .cart .badge{top:-3px;left:8px;margin:0}
.kebab{width:3px;height:10px}
.search{position:absolute;top:56px;left:12px;right:12px;height:25px;border-radius:5px;background:var(--field);display:flex;align-items:center;padding:0 7px;font-size:7px;color:var(--muted)}
.search svg{width:7px;height:7px;margin-right:4px}
.search .mic{margin:0 0 0 auto}
.cat-body{position:absolute;top:98px;left:0;right:0}
.cat-body h3{margin:0 0 0 12px;font-size:9.5px;font-weight:600}
.featured{display:flex;gap:4px;margin:9px 0 0 12px;overflow:hidden}
.feat{flex:none;width:60px}
.feat-img{height:38px;border-radius:2px}
.feat span{display:block;margin-top:4px;font-size:5.5px;line-height:1.3}
.all-title{margin-top:16px !important}
.masonry{display:flex;gap:8px;margin:9px 13px 0}
.masonry .col{flex:1;display:flex;flex-direction:column;gap:9px}
.tile{border-radius:3px;box-shadow:var(--card-shadow);overflow:hidden;background:#fff}
.tile span{display:block;padding:5px 3px 6px;text-align:center;font-size:6.5px;font-weight:600;line-height:1.25}

.map{position:absolute;top:0;left:0;right:0;height:290px;background:linear-gradient(180deg,#6a6a6a 0%,#a7a7a7 25%,#d3d3d3 50%,#cfcfcf 100%)}
.track-head{position:absolute;top:26px;left:10px;right:10px;display:flex;align-items:center;z-index:3}
.round{width:15px;height:15px;border-radius:50%;background:#fff;display:flex;align-items:center;justify-content:center}
.round svg{width:7px;height:7px}
.round.green{background:var(--green);position:relative}
.round.green svg{color:#fff}
.round.green .badge{background:#000;color:#fff;top:-2px;left:9px;margin:0}
.track-head h1{margin:0 0 0 10px;font-size:11px;font-weight:600;color:#fff}
.track-head .actions{margin-left:auto;display:flex;gap:9px}
.vehicle-chip{position:absolute;top:139px;left:72px;width:81px;height:31px;border-radius:3px;background:#1f1f1f;display:flex;align-items:center;padding:0 5px;gap:5px;color:#fff}
.vehicle-chip .dot{width:21px;height:21px;border-radius:50%;background:#fff;display:flex;align-items:center;justify-content:center}
.vehicle-chip .dot svg{width:12px;height:12px}
.vehicle-chip small{display:block;font-size:5px;color:#bbb}
.vehicle-chip b{display:block;font-size:8px;font-weight:600}
.sheet{position:absolute;top:281px;left:0;right:0;bottom:0;background:#fff;border-radius:9px 9px 0 0;padding:12px 10px 0}
.sheet h2{margin:0;font-size:12.5px;font-weight:700}
.eta{margin:4px 0 0;font-size:7.8px;color:#444}
.eta b{color:var(--ink)}
.driver{margin-top:10px;height:40px;border-radius:3px;box-shadow:var(--card-shadow);display:flex;align-items:center;padding:0 8px;gap:6px}
.driver .face{width:25px;height:25px;border-radius:50%;background:linear-gradient(135deg,#2f3f5a,#8fa3bf)}
.driver small{display:block;font-size:5.5px;color:var(--muted)}
.driver b{display:block;font-size:8px;font-weight:600}
.driver i{display:block;font-style:normal;font-size:5px}
.driver i .star{color:var(--green)}
.driver .link{margin-left:auto;font-size:6.5px;color:var(--green)}
.message-row{display:flex;gap:5px;margin-top:13px}
.message{flex:1;height:25px;border-radius:4px;background:var(--field);display:flex;align-items:center;padding:0 7px;font-size:7px;color:#555}
.message svg{width:7px;height:7px;margin-left:auto}
.call{width:25px;height:25px;border-radius:4px;background:var(--field);display:flex;align-items:center;justify-content:center}
.call svg{width:8px;height:8px}

.sign-off{position:absolute;top:1118px;right:61px;font-size:30px;font-weight:800;color:var(--green);letter-spacing:.3px}

.t-wall{background:linear-gradient(135deg,#8c8a86,#d9d6d0 60%,#b7a58c)}
.t-fast{background:linear-gradient(135deg,#34373e,#5b6068 50%,#8fbf5a)}
.t-conc{background:linear-gradient(135deg,#8e9db0,#c9c4bb 50%,#9a948a)}
.t-door{background:linear-gradient(135deg,#e9e9e9,#bdbab4 50%,#f4f4f4)}
.t-steel{background:linear-gradient(90deg,#7f8c99,#c8d0d8 50%,#8a96a3)}
.t-fence{background:linear-gradient(180deg,#6f9a5a,#6fb6d2 60%,#d8d5cc)}
.t-build{background:linear-gradient(160deg,#e7b98a,#c98a55 50%,#2c2c2c)}
.t-timber{background:linear-gradient(135deg,#8d5f36,#d3a36c)}
.t-tools{background:linear-gradient(135deg,#c1392b,#e8c23a 40%,#2e2e2e)}
.t-vac{background:linear-gradient(135deg,#8a8a8a,#d7d7d7 50%,#7a3b3b)}
.t-shelf{background:linear-gradient(135deg,#3b3b3b,#a0a090 50%,#c0392b)}
.t-paint{background:linear-gradient(135deg,#1e2a4a,#8b93a3 60%,#f3f3f3)}
.t-drill{background:linear-gradient(135deg,#f4f4f4,#2aa3b8 55%,#1b1b1b)}
.t-rack{background:linear-gradient(135deg,#fafafa,#b8b8b8 55%,#f0f0f0)}
.t-shop{background:linear-gradient(135deg,#3a4a3a,#d8c64a 45%,#6e7f86)}
</style>
</head>
<body>

<svg class="icon-defs" aria-hidden="true">
  <symbol id="i-home" viewBox="0 0 24 24"><path d="M4 10l8-6 8 6v10H4z" fill="none" stroke="currentColor" stroke-width="2" stroke-linejoin="round"/></symbol>
  <symbol id="i-search" viewBox="0 0 24 24"><circle cx="11" cy="11" r="7" fill="none" stroke="currentColor" stroke-width="2"/><path d="M16 16l5 5" stroke="currentColor" stroke-width="2" stroke-linecap="round"/></symbol>
  <symbol id="i-cart" viewBox="0 0 24 24"><path d="M2 4h3l3 11h11l2-8H7" fill="none" stroke="currentColor" stroke-width="2" stroke-linejoin="round"/><circle cx="9" cy="20" r="1.6" fill="currentColor"/><circle cx="18" cy="20" r="1.6" fill="currentColor"/></symbol>
  <symbol id="i-gear" viewBox="0 0 24 24"><path d="M12 2l8.7 5v10L12 22l-8.7-5V7z" fill="none" stroke="currentColor" stroke-width="2" stroke-linejoin="round"/><circle cx="12" cy="12" r="3" fill="none" stroke="currentColor" stroke-width="2"/></symbol>
  <symbol id="i-menu" viewBox="0 0 24 24"><path d="M3 5h18M3 12h18M3 19h18" stroke="currentColor" stroke-width="2.6" stroke-linecap="round"/></symbol>
  <symbol id="i-pin" viewBox="0 0 24 24"><path d="M12 22s7-7 7-12a7 7 0 10-14 0c0 5 7 12 7 12z" fill="currentColor"/><circle cx="12" cy="10" r="2.6" fill="#fff"/></symbol>
  <symbol id="i-clock" viewBox="0 0 24 24"><circle cx="12" cy="12" r="10" fill="currentColor"/><path d="M12 7v5l3 2" stroke="#fff" stroke-width="2" fill="none" stroke-linecap="round"/></symbol>
  <symbol id="i-chev-down" viewBox="0 0 24 24"><path d="M5 9l7 7 7-7" fill="none" stroke="currentColor" stroke-width="3" stroke-linecap="round" stroke-linejoin="round"/></symbol>
  <symbol id="i-back" viewBox="0 0 24 24"><path d="M15 4l-8 8 8 8" fill="none" stroke="currentColor" stroke-width="3" stroke-linecap="round" stroke-linejoin="round"/></symbol>
  <symbol id="i-kebab" viewBox="0 0 6 24"><circle cx="3" cy="4" r="2.4" fill="currentColor"/><circle cx="3" cy="12" r="2.4" fill="currentColor"/><circle cx="3" cy="20" r="2.4" fill="currentColor"/></symbol>
  <symbol id="i-mic" viewBox="0 0 24 24"><rect x="9" y="2" width="6" height="12" rx="3" fill="none" stroke="currentColor" stroke-width="2"/><path d="M5 11a7 7 0 0014 0M12 18v4" fill="none" stroke="currentColor" stroke-width="2" stroke-linecap="round"/></symbol>
  <symbol id="i-phone" viewBox="0 0 24 24"><path d="M5 3h4l2 5-3 2a11 11 0 006 6l2-3 5 2v4a2 2 0 01-2 2A17 17 0 013 5a2 2 0 012-2z" fill="currentColor"/></symbol>
  <symbol id="i-scooter" viewBox="0 0 24 24"><circle cx="6" cy="18" r="3" fill="currentColor"/><circle cx="18" cy="18" r="3" fill="currentColor"/><path d="M6 15h9l3-8h-3M15 15l-2-6H8" fill="none" stroke="currentColor" stroke-width="2.2" stroke-linecap="round" stroke-linejoin="round"/></symbol>
  <symbol id="i-status" viewBox="0 0 52 12"><rect x="0" y="8" width="2.5" height="4" fill="currentColor"/><rect x="4" y="6" width="2.5" height="6" fill="currentColor"/><rect x="8" y="3" width="2.5" height="9" fill="currentColor"/><rect x="12" y="0" width="2.5" height="12" fill="currentColor"/><path d="M19 5a9 9 0 0112 0M22 8a5 5 0 016 0" fill="none" stroke="currentColor" stroke-width="1.8"/><circle cx="25" cy="11" r="1.2" fill="currentColor"/><rect x="34" y="2" width="16" height="8" rx="2" fill="currentColor"/></symbol>
</svg>

<!-- Top row -->

<section class="phone mini splash" style="left:179px;top:52px">
  <span class="splash-mark">KIT RUNNER...</span>
</section>

<section class="phone mini home" style="left:381px;top:52px">
  <div class="status"><span>9:41</span><svg><use href="#i-status"/></svg></div>
  <header class="app-head"><svg class="menu"><use href="#i-menu"/></svg><span class="wordmark">KIT RUNNER</span><span class="avatar" role="img" aria-label="User profile photo"></span></header>
  <div class="home-body">
    <div class="cat-card">
      <div class="row-title"><h3>Categories</h3><span class="see-all">See All</span></div>
      <div class="cat-grid">
        <div class="cat-item"><div class="cat-thumb t-wall" role="img" aria-label="Ladder against a wall"></div><span>General<br>Hardware</span></div>
        <div class="cat-item"><div class="cat-thumb t-fast" role="img" aria-label="Fasteners and fixings"></div><span>Fasteners<br>&amp; Fixings</span></div>
        <div class="cat-item"><div class="cat-thumb t-conc" role="img" aria-label="Concrete being spread"></div><span>Concrete &amp;<br>Cementing</span></div>
        <div class="cat-item"><div class="cat-thumb t-door" role="img" aria-label="Sliding door hardware"></div><span>Door<br>Hardware</span></div>
      </div>
    </div>
    <div class="hero">
      <h2>Find and order tools and hardware</h2>
      <div class="field"><svg style="color:#111"><use href="#i-pin"/></svg>Enter delivery address</div>
      <div class="field white"><svg style="color:#111"><use href="#i-clock"/></svg>Deliver now<svg class="chev"><use href="#i-chev-down"/></svg></div>
      <div class="find-btn">Find Tools</div>
    </div>
    <div class="section">
      <div class="row-title"><h3>Products we recommend</h3></div>
      <div class="strip">
        <div class="product"><div class="product-img t-paint" role="img" aria-label="Paint tin"></div></div>
        <div class="product"><div class="product-img t-drill" role="img" aria-label="Cordless drill kit"></div></div>
        <div class="product"><div class="product-img t-rack" role="img" aria-label="Steel shelving unit"></div></div>
      </div>
    </div>
  </div>
  <nav class="tabbar">
    <div class="tab on"><svg><use href="#i-home"/></svg>Home</div>
    <div class="tab"><svg><use href="#i-search"/></svg>Browse</div>
    <div class="tab"><svg><use href="#i-cart"/></svg><span class="badge">1</span>Basket</div>
    <div class="tab"><svg><use href="#i-gear"/></svg>Setting</div>
  </nav>
</section>

<section class="phone mini catalogue" style="left:583px;top:52px">
  <div class="status"><span>9:41</span><svg><use href="#i-status"/></svg></div>
  <header class="page-head"><svg class="back"><use href="#i-back"/></svg><h1>Categories</h1>
    <div class="head-actions"><span class="cart"><svg><use href="#i-cart"/></svg><span class="badge">1</span></span><svg class="kebab"><use href="#i-kebab"/></svg></div></header>
  <div class="search"><svg><use href="#i-search"/></svg>Search tools and hardware<svg class="mic"><use href="#i-mic"/></svg></div>
  <div class="cat-body">
    <h3>Featured categories this week</h3>
    <div class="featured">
      <div class="feat"><div class="feat-img t-tools" role="img" aria-label="Assorted power tools"></div><span>Tools</span></div>
      <div class="feat"><div class="feat-img t-vac" role="img" aria-label="Vacuum cleaner"></div><span>Vacuum &amp; Steam Cleaners</span></div>
      <div class="feat"><div class="feat-img t-shelf" role="img" aria-label="Garage shelving"></div><span>Storage &amp; Shelving</span></div>
    </div>
    <h3 class="all-title">All</h3>
    <div class="masonry">
      <div class="col">
        <div class="tile"><div class="t-wall" style="height:50px" role="img" aria-label="Ladder against a wall"></div><span>General Hardware</span></div>
        <div class="tile"><div class="t-conc" style="height:50px" role="img" aria-label="Concrete being spread"></div><span>Concrete &amp; Cementing</span></div>
        <div class="tile"><div class="t-steel" style="height:50px" role="img" aria-label="Corrugated steel sheets"></div><span>Steel &amp; Aluminium Section</span></div>
      </div>
      <div class="col">
        <div class="tile"><div class="t-fast" style="height:105px" role="img" aria-label="Fasteners and fixings"></div><span>Fasteners &amp; Fixings</span></div>
        <div class="tile"><div class="t-door" style="height:50px" role="img" aria-label="Sliding door hardware"></div><span>Door Hardware</span></div>
      </div>
    </div>
  </div>
  <nav class="tabbar">
    <div class="tab"><svg><use href="#i-home"/></svg>Home</div>
    <div class="tab on"><svg><use href="#i-search"/></svg>Browse</div>
    <div class="tab"><svg><use href="#i-cart"/></svg><span class="badge">1</span>Basket</div>
    <div class="tab"><svg><use href="#i-gear"/></svg>Setting</div>
  </nav>
</section>

<section class="phone mini tracking" style="left:785px;top:52px">
  <div class="map" role="img" aria-label="Street map showing the delivery route from store to site"></div>
  <div class="status light"><span>9:41</span><svg><use href="#i-status"/></svg></div>
  <header class="track-head">
    <span class="round"><svg style="color:var(--green)"><use href="#i-back"/></svg></span><h1>Live Tracking</h1>
    <div class="actions"><span class="round green"><svg><use href="#i-cart"/></svg><span class="badge">1</span></span><span class="round"><svg style="color:var(--green);width:3px"><use href="#i-kebab"/></svg></span></div>
  </header>
  <div class="vehicle-chip"><span class="dot"><svg style="color:#111"><use href="#i-scooter"/></svg></span><span><small>Scooty</small><b>BAC-XXXX</b></span></div>
  <div class="sheet">
    <h2>In 05 min</h2>
    <p class="eta">Estimated arrival time: <b>6.00 pm</b></p>
    <div class="driver"><span class="face" role="img" aria-label="Driver profile photo"></span><span><small>Driver Name</small><b>Dale Finch</b><i><span class="star">★</span> 4.5</i></span><span class="link">View Profile ›</span></div>
    <div class="message-row"><div class="message">Send a message...<svg><use href="#i-mic"/></svg></div><div class="call"><svg><use href="#i-phone"/></svg></div></div>
  </div>
</section>

<!-- Bottom row -->

<section class="phone splash" style="left:135px;top:489px;height:419px">
  <span class="splash-mark">KIT RUNNER...</span>
</section>

<section class="phone home" style="left:360px;top:489px;height:613px">
  <div class="status"><span>9:41</span><svg><use href="#i-status"/></svg></div>
  <header class="app-head"><svg class="menu"><use href="#i-menu"/></svg><span class="wordmark">KIT RUNNER</span><span class="avatar" role="img" aria-label="User profile photo"></span></header>
  <div class="home-body">
    <div class="cat-card">
      <div class="row-title"><h3>Categories</h3><span class="see-all">See All</span></div>
      <div class="cat-grid">
        <div class="cat-item"><div class="cat-thumb t-wall" role="img" aria-label="Ladder against a wall"></div><span>General<br>Hardware</span></div>
        <div class="cat-item"><div class="cat-thumb t-fast" role="img" aria-label="Fasteners and fixings"></div><span>Fasteners<br>&amp; Fixings</span></div>
        <div class="cat-item"><div class="cat-thumb t-conc" role="img" aria-label="Concrete being spread"></div><span>Concrete &amp;<br>Cementing</span></div>
        <div class="cat-item"><div class="cat-thumb t-door" role="img" aria-label="Sliding door hardware"></div><span>Door<br>Hardware</span></div>
      </div>
    </div>
    <div class="hero">
      <h2>Find and order tools and hardware</h2>
      <div class="field"><svg style="color:#111"><use href="#i-pin"/></svg>Enter delivery address</div>
      <div class="field white"><svg style="color:#111"><use href="#i-clock"/></svg>Deliver now<svg class="chev"><use href="#i-chev-down"/></svg></div>
      <div class="find-btn">Find Tools</div>
    </div>
    <div class="section">
      <div class="row-title"><h3>Products we recommend</h3></div>
      <div class="strip">
        <div class="product"><div class="product-img t-paint" role="img" aria-label="Paint tin"></div><p>Halden Jet Dry 10L Heavy Duty Glos...</p><div class="price-row"><span class="price">$248.90</span><span class="rate">★ 4.5</span></div></div>
        <div class="product"><div class="product-img t-drill" role="img" aria-label="Cordless drill kit"></div><p>Torvik 18V 2 Piece Brushless...</p><div class="price-row"><span class="price">$299</span><span class="rate">★ 4.5</span></div></div>
        <div class="product"><div class="product-img t-rack" role="img" aria-label="Steel shelving unit"></div><p>Ravelle 1900 x 1900 x 540mm</p><div class="price-row"><span class="price">$203.47</span><span class="rate">★ 4.5</span></div></div>
      </div>
    </div>
    <div class="section" style="margin-top:16px">
      <div class="row-title"><h3>Shops near you</h3><span class="see-all">See All</span></div>
      <div class="strip">
        <div class="product shop"><div class="shop-img t-shop" role="img" aria-label="Hardware store aisle"></div><p>Lorem Ipsum</p><small><svg><use href="#i-pin"/></svg>3 km</small></div>
        <div class="product shop"><div class="shop-img t-shop" role="img" aria-label="Hardware store aisle"></div><p>Lorem Ipsum</p><small><svg><use href="#i-pin"/></svg>3 km</small></div>
        <div class="product shop"><div class="shop-img t-shop" role="img" aria-label="Hardware store aisle"></div><p>Lorem Ipsum</p><small><svg><use href="#i-pin"/></svg>3 km</small></div>
      </div>
    </div>
  </div>
  <nav class="tabbar">
    <div class="tab on"><svg><use href="#i-home"/></svg>Home</div>
    <div class="tab"><svg><use href="#i-search"/></svg>Browse</div>
    <div class="tab"><svg><use href="#i-cart"/></svg><span class="badge">1</span>Basket</div>
    <div class="tab"><svg><use href="#i-gear"/></svg>Setting</div>
  </nav>
</section>

<section class="phone catalogue" style="left:585px;top:489px;height:652px">
  <div class="status"><span>9:41</span><svg><use href="#i-status"/></svg></div>
  <header class="page-head"><svg class="back"><use href="#i-back"/></svg><h1>Categories</h1>
    <div class="head-actions"><span class="cart"><svg><use href="#i-cart"/></svg><span class="badge">1</span></span><svg class="kebab"><use href="#i-kebab"/></svg></div></header>
  <div class="search"><svg><use href="#i-search"/></svg>Search tools and hardware<svg class="mic"><use href="#i-mic"/></svg></div>
  <div class="cat-body">
    <h3>Featured categories this week</h3>
    <div class="featured">
      <div class="feat"><div class="feat-img t-tools" role="img" aria-label="Assorted power tools"></div><span>Tools</span></div>
      <div class="feat"><div class="feat-img t-vac" role="img" aria-label="Vacuum cleaner"></div><span>Vacuum &amp; Steam Cleaners</span></div>
      <div class="feat"><div class="feat-img t-shelf" role="img" aria-label="Garage shelving"></div><span>Storage &amp; Shelving</span></div>
    </div>
    <h3 class="all-title">All</h3>
    <div class="masonry">
      <div class="col">
        <div class="tile"><div class="t-wall" style="height:50px" role="img" aria-label="Ladder against a wall"></div><span>General Hardware</span></div>
        <div class="tile"><div class="t-conc" style="height:50px" role="img" aria-label="Concrete being spread"></div><span>Concrete &amp; Cementing</span></div>
        <div class="tile"><div class="t-steel" style="height:50px" role="img" aria-label="Corrugated steel sheets"></div><span>Steel &amp; Aluminium Section</span></div>
        <div class="tile"><div class="t-build" style="height:105px" role="img" aria-label="Drill on timber boards"></div><span>Building Materials &amp; Supplies</span></div>
      </div>
      <div class="col">
        <div class="tile"><div class="t-fast" style="height:105px" role="img" aria-label="Fasteners and fixings"></div><span>Fasteners &amp; Fixings</span></div>
        <div class="tile"><div class="t-door" style="height:52px" role="img" aria-label="Sliding door hardware"></div><span>Door Hardware</span></div>
        <div class="tile"><div class="t-fence" style="height:52px" role="img" aria-label="Glass pool fencing"></div><span>Fenching &amp; Gates</span></div>
        <div class="tile"><div class="t-timber" style="height:52px" role="img" aria-label="Timber block"></div><span>Timber</span></div>
      </div>
    </div>
  </div>
  <nav class="tabbar">
    <div class="tab"><svg><use href="#i-home"/></svg>Home</div>
    <div class="tab on"><svg><use href="#i-search"/></svg>Browse</div>
    <div class="tab"><svg><use href="#i-cart"/></svg>Basket</div>
    <div class="tab"><svg><use href="#i-gear"/></svg>Setting</div>
  </nav>
</section>

<section class="phone tracking" style="left:810px;top:489px;height:419px">
  <div class="map" role="img" aria-label="Street map showing the delivery route from store to site"></div>
  <div class="status light"><span>9:41</span><svg><use href="#i-status"/></svg></div>
  <header class="track-head">
    <span class="round"><svg style="color:var(--green)"><use href="#i-back"/></svg></span><h1>Live Tracking</h1>
    <div class="actions"><span class="round green"><svg><use href="#i-cart"/></svg><span class="badge">1</span></span><span class="round"><svg style="color:var(--green);width:3px"><use href="#i-kebab"/></svg></span></div>
  </header>
  <div class="vehicle-chip"><span class="dot"><svg style="color:#111"><use href="#i-scooter"/></svg></span><span><small>Scooty</small><b>BAC-XXXX</b></span></div>
  <div class="sheet">
    <h2>In 05 min</h2>
    <p class="eta">Estimated arrival time: <b>6.00 pm</b></p>
    <div class="driver"><span class="face" role="img" aria-label="Driver profile photo"></span><span><small>Driver Name</small><b>Dale Finch</b><i><span class="star">★</span> 4.5</i></span><span class="link">View Profile ›</span></div>
    <div class="message-row"><div class="message">Send a message...<svg><use href="#i-mic"/></svg></div><div class="call"><svg><use href="#i-phone"/></svg></div></div>
  </div>
</section>

<div class="sign-off">KIT RUNNER</div>

</body>
</html>
```